New Web Site Design - Tallow Ridge Communication Solutions

We are looking for a completely new web site design. Tallow Ridge Communication Solutions is a full service company providing PBX and IP/Cloud Based phone systems. We also sell and install video camera surveillance systems and provide low voltage cabling services (CAT5 and CAT3). We are looking for something professional looking. We want to be able to showcase our vendor partners as well as be able to show photos of some of the work we have done. We will also want to be able to post PDF brochures as well as make changes to the website ourselves.

Target Market(s)

Commercial

Industry/Entity Type

Communication

Coding

Coded - Design and coding required

Number of Pages Required

5+ page

Font styles to use
Sans Serif

Colors
0455a3

Requirements
Must have
• Ability to upload PDF brochures
• Professional look and feel
• Ability to upload and easily insert job photos
• Thinking it should have at least 6 pages: Main page, phone systems and services page, carrier services page, video surveillance systems and service page, low voltage cabling services page, contact us page

```html
<!DOCTYPE html>
<html lang="en">
<head>
<meta charset="utf-8">
<title>Tallow Ridge Communication Solutions</title>
<link rel="stylesheet" href="https://fonts.googleapis.com/css2?family=Open+Sans:wght@400;600;700&family=Raleway:wght@300;400;600;700&display=swap">
<style>
:root{
  --navy:#0b3785;
  --navy-deep:#072b6b;
  --brand:#0455a3;
  --button:#2a93db;
  --ink:#222;
  --text:#555;
  --muted:#9a9a9a;
  --band:#e9e9e9;
  --white:#fff;
}
*{box-sizing:border-box;margin:0;padding:0}
html,body{width:1200px;height:2922px;overflow:hidden}
body{position:relative;background:var(--white);font-family:"Open Sans",Arial,sans-serif;color:var(--text)}
.abs{position:absolute}
.heading{font-family:"Raleway",Arial,sans-serif;color:var(--ink);font-weight:600;letter-spacing:.5px}
.btn{display:inline-block;background:var(--button);color:var(--white);font-family:"Open Sans",Arial,sans-serif;font-weight:600;font-size:11px;text-transform:uppercase;border-radius:22px;text-align:center}

/* header */
.site-header{left:0;top:0;width:1200px;height:97px;background:var(--white)}
.brand{left:100px;top:28px}
.brand-name{font-family:"Raleway",Arial,sans-serif;font-weight:600;color:var(--brand);font-size:17px;line-height:1.25}
.nav{right:100px;top:42px;display:flex;gap:46px;font-size:11px;color:#333;text-transform:uppercase}

/* hero */
.hero{left:0;top:97px;width:1200px;height:513px;background:linear-gradient(100deg,#6e6256 0%,#8a8f96 35%,#6f8aa6 60%,#b8c2cc 100%)}
.hero-photo{position:absolute;inset:0}
.hero-copy{left:148px;top:142px;width:520px;color:var(--white)}
.hero-title{font-family:"Raleway",Arial,sans-serif;font-size:30px;line-height:1.3}
.hero-title b{font-weight:700;display:block}
.hero-title span{font-weight:300;display:block}
.hero-text{font-size:15px;line-height:1.75;margin-top:12px;width:490px}
.hero .btn{margin-top:30px;width:190px;line-height:42px;font-size:11px}

/* welcome */
.welcome{left:0;top:672px;width:1200px;text-align:center}
.welcome h1{font-size:27px}
.welcome p{width:860px;margin:24px auto 0;font-size:11px;line-height:2.35}
.service{top:863px;width:304px}
.service-img{width:304px;height:195px}
.service h3{font-family:"Raleway",Arial,sans-serif;font-weight:700;font-size:14px;color:var(--ink);margin-top:24px}
.service p{font-size:11px;line-height:2.35;margin-top:14px}

/* carrier */
.carrier{left:0;top:1273px;width:1200px;height:344px}
.carrier-img{left:0;top:0;width:600px;height:344px;background:linear-gradient(110deg,#c9d6cf 0%,#8aa6b6 45%,#4d6e90 100%)}
.carrier-panel{left:600px;top:0;width:600px;height:344px;background:var(--navy);color:var(--white);text-align:right;padding:62px 92px 0 76px}
.carrier-panel h2{font-family:"Raleway",Arial,sans-serif;font-weight:700;font-size:25px}
.carrier-panel p{font-size:11px;line-height:2.35;margin-top:18px}
.carrier-panel .btn{margin-top:22px;width:172px;line-height:36px;font-size:10px}

/* how it works */
.how-video{left:100px;top:1710px;width:433px;height:291px;background:linear-gradient(135deg,#9aa4ae,#4f5b68 55%,#2a3340)}
.how-copy{left:614px;top:1728px;width:456px}
.how-copy h2{font-size:26px}
.how-copy p{font-size:11px;line-height:2.35;margin-top:18px}
.how-copy .btn{margin-top:26px;width:178px;line-height:44px;font-size:10px}

/* testimonials */
.testimonials{left:0;top:2080px;width:1200px;height:380px;background:var(--band)}
.testimonials h2{position:absolute;left:0;top:52px;width:1200px;text-align:center;font-size:26px}
.quote{top:2218px;width:470px}
.avatar{position:absolute;left:0;top:0;width:118px;height:118px;border-radius:50%;border:4px solid #d4d4d4;background:radial-gradient(circle at 50% 40%,#c9a48a,#6d5a4e 70%)}
.quote-body{position:absolute;left:176px;top:12px;width:262px;font-size:11px;line-height:2.35;font-style:italic;color:#666}
.quote-mark{position:absolute;font-family:Georgia,serif;font-size:44px;color:#c8c8c8;line-height:1}
.quote-author{font-style:normal;margin-top:10px;font-size:11px;color:#777}
.quote-author b{color:var(--navy);font-weight:700}
.dots{left:0;top:2385px;width:1200px;display:flex;justify-content:center;gap:8px}
.dots span{width:6px;height:6px;border-radius:50%;background:#c8c8c8}
.dots span:first-child{background:var(--navy)}

/* partners */
.partners{left:100px;top:2500px;width:1000px;display:flex;justify-content:space-between;align-items:center;font-family:"Raleway",Arial,sans-serif;font-weight:600;font-size:30px;color:#b9b9b9}
.partner{display:flex;align-items:center;gap:10px}
.partner i{display:inline-block;width:38px;height:38px;border-radius:50%;background:#cfcfcf}

/* footer */
.site-footer{left:0;top:2590px;width:1200px;height:280px;background:var(--navy);color:var(--white)}
.footer-col{top:42px}
.footer-col h4{font-family:"Open Sans",Arial,sans-serif;font-weight:700;font-size:12px;text-transform:uppercase}
.footer-links{list-style:none;margin-top:16px;font-size:11px;line-height:25px}
.footer-posts p{font-size:11px;line-height:21px;margin-top:16px;width:265px}
.newsletter p{font-size:11px;margin-top:16px}
.newsletter .field{margin-top:16px;width:268px;height:30px;border-radius:15px;background:var(--navy-deep);font-size:9px;color:#b9c6e0;padding:9px 0 0 22px}
.newsletter .btn{margin-top:14px;width:124px;line-height:30px;font-size:10px}
.footer-partner{font-family:"Open Sans",Arial,sans-serif;font-weight:700;font-size:27px;margin-top:20px;letter-spacing:1px}
.footer-bar{left:0;top:2870px;width:1200px;height:52px;background:var(--navy-deep);color:var(--white);font-size:11px}
.footer-bar .copy{left:100px;top:18px}
.social{right:100px;top:20px;display:flex;gap:24px}
.social span{width:12px;height:12px;border-radius:50%;background:var(--white)}
</style>
</head>
<body>

<header class="site-header abs">
  <div class="brand abs">
    <span class="brand-name">Tallow Ridge<br>Communication Solutions</span>
  </div>
  <nav class="nav abs">
    <span>Home</span><span>Phone Systems</span><span>Carrier</span><span>Video Surveillance</span><span>Low Voltage Cabling</span><span>Contact Us</span>
  </nav>
</header>

<section class="hero abs">
  <div class="hero-photo" role="img" aria-label="Hand holding a smartphone showing a home automation app, blurred office buildings behind"></div>
  <div class="hero-copy abs">
    <h1 class="hero-title"><b>WE PROVIDE PBX AND</b><span>IP/CLOUD BASED PHONE SYSTEMS</span></h1>
    <p class="hero-text">We also sell and install video camera surveillance systems and provide low voltage cabling services (CAT5 and CAT3).</p>
    <span class="btn">Click here for info</span>
  </div>
</section>

<section class="welcome abs">
  <h1 class="heading">WELCOME TO TALLOW RIDGE COMMUNICATIONS</h1>
  <p>Lorem Ipsum is simply dummy text of the printing and typesetting industry. Lorem Ipsum has been the industry's standard dummy text ever since the 1500s, when an unknown printer took a galley of type and scrambled it to make a type specimen book. It has survived not only five centuries, but also the leap into electronic typesetting, remaining essentially unchanged</p>
</section>

<article class="service abs" style="left:100px">
  <div class="service-img" role="img" aria-label="Hand holding a phone in front of a house" style="background:linear-gradient(135deg,#e7d8c4,#9bb3c8 60%,#5e7188)"></div>
  <h3>PHONE SYSTEMS</h3>
  <p>Lorem Ipsum is simply dummy text of the printing and typesetting industry. Lorem Ipsum has been the industry's standard dummy...</p>
</article>
<article class="service abs" style="left:449px">
  <div class="service-img" role="img" aria-label="Ceiling mounted security camera" style="background:linear-gradient(160deg,#f1f3f4,#c4cbd0 60%,#8e979e)"></div>
  <h3>VIDEO SURVEILLANCE</h3>
  <p>Lorem Ipsum is simply dummy text of the printing and typesetting industry. Lorem Ipsum has been the industry's standard dummy...</p>
</article>
<article class="service abs" style="left:798px">
  <div class="service-img" role="img" aria-label="Technician working on a network cabling rack" style="background:linear-gradient(120deg,#4a5563,#2a3039 50%,#8a94a0)"></div>
  <h3>LOW VOLTAGE CABLING</h3>
  <p>Lorem Ipsum is simply dummy text of the printing and typesetting industry. Lorem Ipsum has been the industry's standard dummy...</p>
</article>

<section class="carrier abs">
  <div class="carrier-img abs" role="img" aria-label="Three colleagues working together at a laptop"></div>
  <div class="carrier-panel abs">
    <h2>CARRIER</h2>
    <p>Lorem Ipsum is simply dummy text of the printing and typesetting industry. Lorem Ipsum has been the industry's standard dummy text ever since the 1500s, when an unknown printer took a galley of type and scrambled it to make a type specimen book. It has survived not only five centuries...</p>
    <span class="btn">Click here for info</span>
  </div>
</section>

<div class="how-video abs" role="img" aria-label="Video still of a businessman touching a circuit interface">
  <svg width="433" height="291" viewBox="0 0 433 291">
    <circle cx="216" cy="145" r="36" fill="#e2463f"/>
    <path d="M204 127 L234 145 L204 163 Z" fill="#fff"/>
  </svg>
</div>
<section class="how-copy abs">
  <h2 class="heading">HOW IT WORKS</h2>
  <p>Lorem Ipsum is simply dummy text of the printing and typesetting industry. Lorem Ipsum has been the industry's standard dummy text ever since the 1500s, when an unknown printer took a galley of type and scrambled it to make a type specimen book. It has survived not only five centuries, but also the leap into electronic typesetting, remaining essentially unchanged.</p>
  <span class="btn">Click here for info</span>
</section>

<section class="testimonials abs">
  <h2 class="heading">TESTIMONIALS</h2>
</section>
<figure class="quote abs" style="left:112px">
  <div class="avatar" role="img" aria-label="Portrait of a smiling client"></div>
  <span class="quote-mark" style="left:150px;top:0">&ldquo;</span>
  <blockquote class="quote-body">Lorem Ipsum is simply dummy text of the printing and typesetting industry. Lorem Ipsum has been the industry's standard dummy text ever...
    <div class="quote-author"><b>MARLON VESEY</b> - Business man -</div>
  </blockquote>
  <span class="quote-mark" style="left:428px;top:92px">&rdquo;</span>
</figure>
<figure class="quote abs" style="left:643px">
  <div class="avatar" role="img" aria-label="Portrait of a smiling client"></div>
  <span class="quote-mark" style="left:150px;top:0">&ldquo;</span>
  <blockquote class="quote-body">Lorem Ipsum is simply dummy text of the printing and typesetting industry. Lorem Ipsum has been the industry's standard dummy text ever...
    <div class="quote-author"><b>MARLON VESEY</b> - Business man -</div>
  </blockquote>
  <span class="quote-mark" style="left:428px;top:92px">&rdquo;</span>
</figure>
<div class="dots abs"><span></span><span></span><span></span></div>

<section class="partners abs">
  <span class="partner">Pinefold</span>
  <span class="partner"><i></i>Corvel Works</span>
  <span class="partner">NORIX</span>
  <span class="partner">ALDEN</span>
  <span class="partner"><i></i>Quenmar</span>
</section>

<footer class="site-footer abs">
  <div class="footer-col abs" style="left:100px">
    <h4>Welcome</h4>
    <ul class="footer-links">
      <li>Home</li><li>Phone systems</li><li>Carrier</li><li>Video Surveillance</li><li>Low voltage cabling</li><li>Contact us</li>
    </ul>
  </div>
  <div class="footer-col footer-posts abs" style="left:350px">
    <h4>Latest News</h4>
    <p>Lorem Ipsum is simply dummy text of the printing and typesetting industry</p>
    <p>Lorem Ipsum is simply dummy text of the printing and typesetting industry</p>
    <p>Lorem Ipsum is simply dummy text of the printing and typesetting industry</p>
  </div>
  <div class="footer-col newsletter abs" style="left:762px">
    <h4>Newsletter Signup</h4>
    <p>Get our recent updates through your email id</p>
    <div class="field">Enter your email id</div>
    <span class="btn">Subscribe</span>
    <div class="footer-partner">KORVANE</div>
  </div>
</footer>
<div class="footer-bar abs">
  <span class="copy abs">Copyrights 2015. Tallow Ridge Communications.&nbsp; All rights reserved.</span>
  <div class="social abs"><span></span><span></span><span></span><span></span><span></span><span></span></div>
</div>

</body>
</html>
```